Business Card Design for Software Development Company

I am looking for a business card design the incorporates my new logo (attached below).

Key information to include:
Name: Martin Quelbrook
Title: CEO
Email: martin@brightwellcivic.example
Phone: 555-218-9403
Website: www.brightwellcivic.example

NOTE: This design should be easy to edit so that we can order cards for different members of our team.

```html
<!DOCTYPE html>
<html lang="en">
<head>
<meta charset="utf-8">
<title>Brightwell Labs – Business Card</title>
<link rel="stylesheet" href="https://fonts.googleapis.com/css2?family=Montserrat:wght@400;500;700&display=swap">
<style>
  :root {
    --backdrop: #1d1d1d;
    --card-white: #f4f4f3;
    --ink: #232323;
    --teal: #14ac98;
    --orange: #e37b28;
    --orange-soft: #f0d9c6;
    --teal-soft: #bfe6de;
    --rose-soft: #ecc9cb;
  }
  * { margin: 0; padding: 0; box-sizing: border-box; }
  html, body { width: 1200px; height: 1059px; overflow: hidden; }
  body {
    background: var(--backdrop);
    font-family: "Montserrat", sans-serif;
    position: relative;
  }
  .card {
    position: absolute;
    width: 690px;
    height: 392px;
    border-radius: 24px;
    overflow: hidden;
  }
  .card--front { left: 255px; top: 89px; background: var(--card-white); }
  .card--back { left: 255px; top: 547px; background: var(--orange); }

  .brand-graphic {
    position: absolute;
    right: 0; top: 0;
    width: 380px; height: 392px;
    background: linear-gradient(200deg, var(--teal-soft) 0%, var(--rose-soft) 35%, var(--orange-soft) 65%, rgba(244,244,243,0) 100%);
    opacity: .75;
    clip-path: polygon(0 0, 100% 0, 100% 100%, 40% 100%);
  }

  .wordmark {
    position: absolute;
    display: flex;
    align-items: center;
    gap: 10px;
  }
  .wordmark__square { width: 22px; height: 22px; }
  .wordmark__name { font-weight: 700; letter-spacing: -1px; line-height: 1; white-space: nowrap; }
  .wordmark__tagline {
    position: absolute;
    right: 0;
    font-weight: 700;
    text-transform: uppercase;
    white-space: nowrap;
  }

  .card--front .wordmark { left: 37px; top: 66px; }
  .card--front .wordmark__square { background: var(--teal); }
  .card--front .wordmark__name { font-size: 38px; color: var(--ink); }
  .card--front .wordmark__tagline { top: 46px; font-size: 5.5px; color: var(--ink); letter-spacing: .3px; }

  .card--back .wordmark { left: 50%; top: 168px; transform: translateX(-50%); }
  .card--back .wordmark__square { width: 30px; height: 30px; background: #fff; }
  .card--back .wordmark__name { font-size: 54px; color: #fff; }
  .card--back .wordmark__tagline { top: 64px; font-size: 8px; color: #fff; letter-spacing: .4px; }

  .name-tab {
    position: absolute; left: 0; top: 188px;
    width: 16px; height: 41px;
    background: var(--teal);
    border-radius: 0 4px 4px 0;
  }
  .person { position: absolute; left: 37px; top: 184px; }
  .person__name { font-size: 23px; font-weight: 700; text-transform: uppercase; letter-spacing: .2px; }
  .person__first { color: var(--teal); }
  .person__last { color: var(--orange); }
  .person__title { font-size: 18px; font-weight: 400; color: var(--ink); margin-top: 2px; }

  .contact { position: absolute; left: 37px; top: 263px; list-style: none; }
  .contact__item {
    display: flex; align-items: center; gap: 9px;
    height: 33px;
    font-size: 17.5px; color: var(--ink);
  }
  .contact__icon { width: 14px; height: 14px; flex: none; }
</style>
</head>
<body>
  <section class="card card--front">
    <div class="brand-graphic" role="img" aria-label="Soft layered brand colour graphic in teal, rose and peach"></div>

    <div class="wordmark">
      <span class="wordmark__square"></span>
      <span class="wordmark__name">Brightwell Labs</span>
      <span class="wordmark__tagline">A division of Brightwell Civic</span>
    </div>

    <span class="name-tab"></span>
    <div class="person">
      <p class="person__name"><span class="person__first">Martin</span> <span class="person__last">Quelbrook</span></p>
      <p class="person__title">CEO</p>
    </div>

    <ul class="contact">
      <li class="contact__item">
        <svg class="contact__icon" viewBox="0 0 14 14" aria-hidden="true"><path d="M1 5c0-2 3-3 6-3s6 1 6 3v1h-3V5H4v1H1z M3 7h8l1 5H2z" fill="#efb98a"/></svg>
        <span>555-218-9403</span>
      </li>
      <li class="contact__item">
        <svg class="contact__icon" viewBox="0 0 14 14" aria-hidden="true"><path d="M1 6l6-4 6 4v7H1z" fill="#14ac98"/><path d="M1 6l6 4 6-4" fill="none" stroke="#fff" stroke-width="1"/></svg>
        <span>martin@brightwellcivic.example</span>
      </li>
      <li class="contact__item">
        <svg class="contact__icon" viewBox="0 0 14 14" aria-hidden="true"><circle cx="7" cy="7" r="6" fill="#e37b28"/><path d="M4 4c2 0 2 2 1 3s1 3 2 3M9 3c0 2 2 2 3 2" fill="none" stroke="#fff" stroke-width="1.2"/></svg>
        <span>www.brightwellcivic.example</span>
      </li>
    </ul>
  </section>

  <section class="card card--back">
    <div class="wordmark">
      <span class="wordmark__square"></span>
      <span class="wordmark__name">Brightwell Labs</span>
      <span class="wordmark__tagline">A division of Brightwell Civic</span>
    </div>
  </section>
</body>
</html>
```